Brimsett Gardening Fresh New Website

We are looking to create a simple fresh website for our landscaping business. The website should appeal to a 'high end' audience. We deal with a lot of Embassies and affluent clients who have extremely large gardens that are meticulously maintained. The site is about communicating our excellent landscaping and customer service skills and encouraging new clients to reach out and engage us to take care of their gardens.

The website is basically going to be our business card, it will have almost no functionality other than two 'contact us' forms, one for smaller clients and one for more detailed projects.

The website will not have a lot of written content and will have to show photos of beautifully landscaped gardens.

The main logo in black will influence the site, however, we are open to all suggestions.

We are expecting to have the following pages:
Home Page
Services
About Us
Contact Us
Showcase (photo gallery of our work)

We need someone who can code it to wordpress and be available for minor changes over a number of days. They will be simple tweaks.

```html
<!DOCTYPE html>
<html lang="en">
<head>
<meta charset="utf-8">
<title>Brimsett Gardening</title>
<link href="https://fonts.googleapis.com/css2?family=Libre+Caslon+Text:wght@400;700&family=Lato:wght@400;700&display=swap" rel="stylesheet">
<style>
:root{
  --ink:#1b1917;
  --ink-soft:#2a211b;
  --footer:#2b2a29;
  --gold:#f5d349;
  --gold-deep:#c89a2c;
  --white:#ffffff;
  --muted:#d9d4cc;
  --line:#8a8680;
  --leaf:#5d9a2e;
  --leaf-light:#9cc94a;
  --leaf-dark:#24401a;
  --soil:#4a3526;
  --serif:"Libre Caslon Text", Georgia, serif;
  --sans:"Lato", Arial, sans-serif;
}
*{box-sizing:border-box;margin:0;padding:0}
html,body{width:1200px;height:4412px;overflow:hidden}
body{position:relative;background:var(--ink);font-family:var(--sans);color:var(--white)}
.abs{position:absolute}
.btn{position:absolute;display:flex;align-items:center;justify-content:center;border-radius:24px;
  background:linear-gradient(90deg,var(--gold),var(--gold-deep));color:#3a2c10;font-family:var(--serif);
  font-weight:700;font-size:13px;letter-spacing:.3px}
.photo{position:absolute;overflow:hidden}
h2.section-title{position:absolute;font-family:var(--serif);font-weight:700;font-size:32px;letter-spacing:-.5px;color:var(--white)}

/* header */
.topbar{left:300px;top:0;width:900px;height:52px;background:var(--gold);display:flex;align-items:center;padding-left:42px;color:#2a2110;font-family:var(--serif);font-size:13px;font-weight:700}
.topbar .item{display:flex;align-items:center;gap:8px;margin-right:40px}
.topbar .socials{position:absolute;right:112px;top:8px;display:flex;gap:12px}
.topbar .socials span{width:36px;height:36px;border:2px solid #2a2110;border-radius:50%;display:flex;align-items:center;justify-content:center}
.topbar .socials span::after{content:"";width:10px;height:10px;border-radius:50%;background:#2a2110}
.brand{left:100px;top:20px;width:140px;text-align:center;color:var(--gold-deep);font-family:var(--serif)}
.brand .dot{width:24px;height:24px;border:1.5px solid var(--gold-deep);border-radius:50%;margin:0 auto 14px}
.brand .name{font-size:17px;letter-spacing:6px}
.brand .sub{font-size:8px;letter-spacing:5px;margin-top:4px}
.nav{left:320px;top:89px;display:flex;font-size:15px}
.nav a{color:var(--white);text-decoration:none;margin-right:52px}

/* hero */
.hero{left:0;top:143px;width:1200px;height:660px;background:
  radial-gradient(ellipse 260px 200px at 620px 90px,rgba(40,80,80,.85),transparent 70%),
  radial-gradient(ellipse 220px 160px at 220px 60px,rgba(190,180,160,.55),transparent 70%),
  radial-gradient(ellipse 300px 160px at 820px 420px,rgba(225,215,195,.55),transparent 70%),
  radial-gradient(ellipse 260px 260px at 1100px 420px,rgba(110,160,50,.7),transparent 70%),
  radial-gradient(ellipse 300px 200px at 560px 480px,rgba(90,140,40,.55),transparent 70%),
  linear-gradient(180deg,#3a3a30 0%,#4e3a2a 55%,#3a2a1e 100%)}
.hero-shade{left:0;top:143px;width:760px;height:660px;background:linear-gradient(90deg,rgba(20,18,14,.65),rgba(20,18,14,0))}
.hero-curve{left:0;top:600px}
.hero-kicker{left:114px;top:284px;font-family:var(--serif);font-weight:700;font-size:31px;letter-spacing:-.5px}
.hero-title{left:112px;top:345px;font-family:var(--serif);font-weight:700;font-size:54px;letter-spacing:-1px;color:var(--gold)}
.hero-text{left:115px;top:430px;width:460px;font-size:18px;line-height:27px}

/* services */
.svc-frame{left:112px;top:908px;width:506px;height:632px;background:linear-gradient(160deg,#3d6a26,#1a3a12 60%,#0f2a0c);border-radius:4px}
.svc-photo{left:162px;top:960px;width:456px;height:580px;background:
  radial-gradient(ellipse 110px 120px at 150px 200px,rgba(160,205,80,.95),transparent 70%),
  radial-gradient(ellipse 140px 60px at 230px 460px,rgba(230,170,140,.8),transparent 70%),
  radial-gradient(ellipse 90px 40px at 180px 390px,rgba(60,40,25,.85),transparent 70%),
  radial-gradient(circle at 70% 20%,#c8d870,transparent 40%),
  linear-gradient(160deg,#7ea848,#3f6b22 55%,#1f3512)}
.svc-item{right:113px;width:390px;text-align:right}
.svc-item h3{font-family:var(--serif);font-weight:700;font-size:22px;margin-right:115px}
.svc-item p{font-size:14px;line-height:23.5px;color:var(--muted);width:268px;margin:18px 0 0 7px;text-align:justify;text-align-last:right}
.svc-icon{position:absolute;right:0;top:-8px;width:72px;height:84px;background:var(--gold);border-radius:4px 4px 36px 36px;display:flex;align-items:center;justify-content:center}

/* contact band */
.touch{left:0;top:1645px;width:1200px;height:470px;background:
  radial-gradient(ellipse 300px 200px at 850px 150px,rgba(230,200,110,.5),transparent 70%),
  radial-gradient(ellipse 400px 200px at 200px 400px,rgba(150,110,30,.5),transparent 70%),
  linear-gradient(120deg,#c69a32,#b28a2c 50%,#c8a03a)}
.field{position:absolute;height:63px;border-radius:32px;background:var(--white);color:#333;font-size:15px;display:flex;align-items:center;padding-left:30px}

/* about */
.about-text{left:112px;top:2292px;width:430px;font-size:14.5px;line-height:25.7px;text-align:justify}
.about-photo{left:602px;top:2222px;width:489px;height:363px;border-radius:30px;background:
  radial-gradient(ellipse 90px 70px at 230px 90px,rgba(150,200,70,.9),transparent 70%),
  radial-gradient(ellipse 70px 60px at 420px 300px,rgba(170,60,160,.8),transparent 70%),
  radial-gradient(ellipse 60px 60px at 430px 120px,rgba(230,210,60,.8),transparent 70%),
  radial-gradient(ellipse 90px 90px at 40px 200px,rgba(60,60,80,.7),transparent 70%),
  radial-gradient(ellipse 160px 60px at 260px 290px,rgba(80,55,40,.85),transparent 70%),
  radial-gradient(ellipse 200px 120px at 300px 20px,rgba(220,190,110,.7),transparent 70%),
  linear-gradient(160deg,#6f8b3e,#4f6d2a 60%,#4a3a2a)}

/* showcase */
.showcase{left:0;top:2687px;width:1200px;height:753px;background:var(--ink-soft)}
.tile{position:absolute;width:307px;height:252px}

/* booking */
.book-circle{left:117px;top:3542px;width:380px;height:380px;border-radius:50%;border:4px solid var(--gold);background:
  radial-gradient(ellipse 90px 60px at 150px 230px,rgba(130,135,100,.9),transparent 70%),
  radial-gradient(ellipse 80px 150px at 290px 230px,rgba(90,70,40,.85),transparent 70%),
  radial-gradient(ellipse 70px 80px at 110px 90px,rgba(150,110,190,.6),transparent 70%),
  linear-gradient(135deg,#c8cf70,#6d8a3c 50%,#3f5a22)}
.book-title{left:560px;top:3540px;font-family:var(--serif);font-weight:700;font-size:31px;line-height:46px;letter-spacing:-.5px}
.uline{position:absolute;border-bottom:1.5px solid var(--line);font-size:14px;padding:0 0 12px 6px}

/* footer */
.footer{left:0;top:4025px;width:1200px;height:387px;background:var(--footer)}
.foot-brand{left:0;top:4085px;width:1200px;text-align:center;font-family:var(--serif)}
.foot-brand .dot{width:28px;height:28px;border:1.5px solid var(--white);border-radius:50%;margin:0 auto 20px}
.foot-brand .name{font-size:22px;letter-spacing:9px}
.foot-brand .sub{font-size:11px;letter-spacing:6px;margin-top:4px}
.foot-nav{left:0;top:4242px;width:1200px;display:flex;justify-content:center;font-size:14px}
.foot-nav span{margin:0 22px}
.foot-social{left:0;top:4298px;width:1200px;display:flex;justify-content:center;gap:7px}
.foot-social span{width:36px;height:36px;border:2px solid var(--white);border-radius:50%;display:flex;align-items:center;justify-content:center}
.foot-social span::after{content:"";width:10px;height:10px;border-radius:50%;background:var(--white)}
.copy{left:0;top:4358px;width:1200px;text-align:center;font-size:15px}
</style>
</head>
<body>

<!-- header -->
<div class="abs brand"><div class="dot"></div><div class="name">BRIMSETT</div><div class="sub">GARDENING</div></div>
<div class="abs topbar">
  <div class="item">
    <svg width="18" height="18" viewBox="0 0 24 24" fill="none" stroke="#2a2110" stroke-width="2"><path d="M5 3h4l2 5-3 2a12 12 0 0 0 6 6l2-3 5 2v4a2 2 0 0 1-2 2A17 17 0 0 1 3 5a2 2 0 0 1 2-2z"/></svg>
    PHONE : +1 (555) 014 2287
  </div>
  <div class="item">
    <svg width="20" height="16" viewBox="0 0 24 18" fill="none" stroke="#2a2110" stroke-width="2"><rect x="1" y="1" width="22" height="16"/><path d="M1 1l11 9 11-9"/></svg>
    EMAIL : info@brimsettgardening.com
  </div>
  <div class="socials"><span></span><span></span><span></span></div>
</div>
<nav class="abs nav"><a>HOME</a><a>SERVICES</a><a>ABOUT US</a><a>CONTACT US</a><a>SHOWCASE</a></nav>
<div class="btn" style="left:984px;top:75px;width:104px;height:46px;">LOG IN</div>

<!-- hero -->
<div class="photo hero" role="img" aria-label="Gloved hands planting seedlings in garden soil beside a watering can"></div>
<div class="abs hero-shade"></div>
<svg class="abs hero-curve" width="1200" height="230" viewBox="0 0 1200 230">
  <path d="M0 50 Q600 330 1200 40 L1200 230 L0 230 Z" fill="var(--ink)"/>
  <path d="M0 50 Q600 330 1200 40" fill="none" stroke="var(--gold)" stroke-width="5"/>
  <circle cx="600" cy="191" r="30" fill="var(--gold)"/>
  <path d="M589 186l11 11 11-11" fill="none" stroke="#2a2110" stroke-width="3"/>
</svg>
<div class="abs hero-kicker">WLCOME TO</div>
<div class="abs hero-title">BRIMSETT GARDENING</div>
<p class="abs hero-text">Lorem ipsum dolor sit amet, consectetur adipiscing elit, sed do eiusmod tempor incididunt ut labore et dolore magna aliqua.</p>
<div class="btn" style="left:115px;top:549px;width:123px;height:43px;">LEARN MORE</div>

<!-- services -->
<div class="photo svc-frame" role="img" aria-label="Blurred green garden backdrop"></div>
<div class="photo svc-photo" role="img" aria-label="Hands holding a young seedling in soil"></div>
<h2 class="section-title" style="right:113px;top:958px;">OUR SERVICES</h2>
<div class="abs svc-item" style="top:1052px;">
  <h3>Lorem ipsum dolor</h3>
  <p>Lorem ipsum dolor sit amet, consectetur adipiscing elit, sed do eiusmod tempor incididunt ut labore et dolore magna aliqua.</p>
  <div class="svc-icon"><svg width="40" height="36" viewBox="0 0 40 36" fill="none" stroke="#2a2110" stroke-width="2"><path d="M4 14L20 3l16 11"/><path d="M8 14v16M14 14v16M20 14v16M26 14v16M32 14v16"/><path d="M3 32h34"/></svg></div>
</div>
<div class="abs svc-item" style="top:1264px;">
  <h3>Lorem ipsum dolor</h3>
  <p>Lorem ipsum dolor sit amet, consectetur adipiscing elit, sed do eiusmod tempor incididunt ut labore et dolore magna aliqua.</p>
  <div class="svc-icon"><svg width="40" height="38" viewBox="0 0 40 38" fill="none" stroke="#2a2110" stroke-width="2"><path d="M6 14h28v20H6z"/><path d="M4 14l4-8h24l4 8"/><rect x="11" y="20" width="7" height="14"/><rect x="23" y="20" width="7" height="7"/></svg></div>
</div>
<div class="btn" style="left:965px;top:1463px;width:122px;height:45px;">VIEW ALL</div>

<!-- get in touch -->
<div class="photo touch" role="img" aria-label="Warm golden-toned garden scene behind the contact form"></div>
<h2 class="section-title" style="left:0;width:1200px;text-align:center;top:1722px;">GET IN TOUCH</h2>
<div class="field" style="left:188px;top:1802px;width:400px;">Name</div>
<div class="field" style="left:611px;top:1802px;width:400px;">Email</div>
<div class="field" style="left:188px;top:1888px;width:821px;">Phone</div>
<div class="btn" style="left:538px;top:1983px;width:123px;height:44px;">SUBMIT</div>

<!-- about -->
<h2 class="section-title" style="left:112px;top:2222px;">ABOUT US</h2>
<p class="abs about-text">Lorem ipsum dolor sit amet, consectetur adipiscing elit, sed do eiusmod tempor incididunt ut labore et dolore magna aliqua. Ut enim ad minim veniam, quis nostrud exercitation ullamco laboris nisi ut aliquip ex ea commodo consequat. Duis aute irure dolor in reprehenderit in voluptate velit esse cillum dolore eu fugiat nulla pariatur. Excepteur sint occaecat cupidatat non proident, sunt in culpa qui officia deserunt mollit anim id est laborum.</p>
<div class="btn" style="left:112px;top:2536px;width:132px;height:43px;">LEARN MORE</div>
<div class="photo about-photo" role="img" aria-label="Gardener in gloves planting flowers in a colourful bed"></div>

<!-- showcase -->
<div class="abs showcase"></div>
<h2 class="section-title" style="left:0;width:1200px;text-align:center;top:2755px;">SHOWCASE</h2>
<div class="photo tile" style="left:112px;top:2835px;background:radial-gradient(ellipse 120px 60px at 100px 190px,rgba(220,80,120,.8),transparent 70%),radial-gradient(ellipse 90px 50px at 240px 40px,rgba(220,110,140,.6),transparent 70%),radial-gradient(ellipse 160px 90px at 200px 140px,#8fd040,transparent 70%),linear-gradient(160deg,#3f6a22,#6aa832 50%,#4f8a28);" role="img" aria-label="Curving lawn edged with flower beds"></div>
<div class="photo tile" style="left:446px;top:2835px;background:radial-gradient(ellipse 70px 110px at 60px 80px,rgba(150,150,150,.7),transparent 70%),radial-gradient(ellipse 60px 50px at 180px 140px,rgba(240,240,230,.8),transparent 70%),radial-gradient(ellipse 150px 60px at 150px 220px,rgba(70,50,35,.9),transparent 70%),linear-gradient(160deg,#c8d890,#6e9a3a 50%,#4a3a2a);" role="img" aria-label="Gardener planting a seedling"></div>
<div class="photo tile" style="left:780px;top:2835px;background:radial-gradient(ellipse 60px 70px at 80px 100px,rgba(170,60,60,.7),transparent 70%),radial-gradient(ellipse 80px 60px at 220px 90px,rgba(160,70,60,.6),transparent 70%),radial-gradient(ellipse 160px 60px at 150px 200px,#6fb03a,transparent 70%),linear-gradient(180deg,#6a6048,#7a6a52 40%,#4f7a2a);" role="img" aria-label="Family tending a vegetable patch"></div>
<div class="photo tile" style="left:112px;top:3108px;background:radial-gradient(ellipse 180px 80px at 120px 30px,rgba(240,235,190,.8),transparent 70%),radial-gradient(ellipse 60px 80px at 170px 130px,rgba(120,90,70,.6),transparent 70%),radial-gradient(ellipse 200px 70px at 150px 210px,#5f8f2e,transparent 70%),linear-gradient(180deg,#a8ae70,#6f8a3a 50%,#3d5a1e);" role="img" aria-label="People working in a raised-bed vegetable garden"></div>
<div class="photo tile" style="left:446px;top:3108px;background:radial-gradient(ellipse 70px 100px at 130px 120px,rgba(150,150,130,.8),transparent 70%),radial-gradient(ellipse 160px 70px at 150px 220px,#8cc85a,transparent 70%),radial-gradient(ellipse 160px 90px at 230px 40px,rgba(230,245,190,.8),transparent 70%),linear-gradient(160deg,#b8d08a,#6e9a40 50%,#4a6a2a);" role="img" aria-label="Gardener watering plants in a sunny garden"></div>
<div class="photo tile" style="left:780px;top:3108px;background:radial-gradient(ellipse 60px 90px at 190px 110px,rgba(235,110,40,.9),transparent 70%),radial-gradient(ellipse 70px 50px at 220px 170px,rgba(60,110,40,.9),transparent 70%),radial-gradient(ellipse 100px 60px at 80px 190px,rgba(140,60,80,.6),transparent 70%),linear-gradient(160deg,#a8b850,#5e8a2e 50%,#7ab040);" role="img" aria-label="Landscaper planting shrubs on a lawn"></div>

<!-- booking -->
<div class="photo book-circle" role="img" aria-label="Parent and child watering plants together in a garden"></div>
<h2 class="abs book-title">BOOK NOW FOR LANDSCAPE<br>PROJECTS</h2>
<div class="uline" style="left:560px;top:3665px;width:252px;">First Name :</div>
<div class="uline" style="left:832px;top:3665px;width:253px;">Last Name :</div>
<div class="uline" style="left:560px;top:3733px;width:252px;">Email :</div>
<div class="uline" style="left:832px;top:3733px;width:253px;">Phone :</div>
<div class="uline" style="left:560px;top:3811px;width:525px;">Message :</div>
<div class="btn" style="left:560px;top:3884px;width:131px;height:44px;">SUBMIT</div>

<!-- footer -->
<div class="abs footer"></div>
<div class="abs foot-brand"><div class="dot"></div><div class="name">BRIMSETT</div><div class="sub">GARDENING</div></div>
<div class="abs foot-nav"><span>HOME</span><span>SERVICES</span><span>ABOUT US</span><span>CONTACT US</span><span>SHOWCASE</span></div>
<div class="abs foot-social"><span></span><span></span><span></span><span></span><span></span></div>
<div class="abs copy">©Copyrights 2024 Brimsett Gardening &nbsp; | &nbsp; All Rights Reserved</div>

</body>
</html>
```